Property Developer Business card design

we need a business card design + printing for a new Property developer company based in melbourne.
We are a group of investors investing in a property developer business. We have more projects involved in residential property as opposed to commercial property but we are involved in both market. we also provide consulting services with overseas investors willing to invest in the australian property market.
Updates
I have uploaded the logo. I'm not very convince with the colors of my logo... any suggestion please?.
Thanks guys!
Target Market(s)
property investors or person willing to purchase investment property
Industry/Entity Type
Residential
Contact Information for Business Card
Bramblecourt Holdings Australia Pty Ltd
Look and feel

```html
<!DOCTYPE html>
<html lang="en">
<head>
<meta charset="utf-8">
<title>Bramblecourt Holdings Australia – Business Card</title>
<link rel="stylesheet" href="https://fonts.googleapis.com/css2?family=Josefin+Sans:wght@400;600&family=Tinos&display=swap">
<style>
  :root {
    --bg: #e4e4e4;
    --card-white: #ffffff;
    --card-black: #050505;
    --brand-red: #bd2227;
    --brand-blue: #1e86c9;
    --brand-sky: #2aa3dc;
    --ink: #111111;
    --font-main: "Josefin Sans", Arial, sans-serif;
    --font-serif: "Tinos", "Times New Roman", serif;
  }
  * { margin: 0; padding: 0; box-sizing: border-box; }
  html, body { width: 1200px; height: 985px; overflow: hidden; }
  body { background: var(--bg); position: relative; font-family: var(--font-main); }

  .card {
    position: absolute;
    width: 620px;
    height: 378px;
    border-radius: 26px;
    overflow: hidden;
    box-shadow: 0 10px 24px rgba(0,0,0,0.18);
  }
  .card-waves { position: absolute; inset: 0; width: 100%; height: 100%; }

  /* Back side */
  .card-back { left: 500px; top: 60px; background: var(--card-black); }
  .card-back .brand {
    position: absolute; left: 0; right: 0; top: 92px;
    display: flex; align-items: center; justify-content: center; gap: 14px;
  }
  .brand-dot { width: 18px; height: 18px; border-radius: 50%; background: var(--brand-red); flex: none; }
  .brand-name {
    font-family: var(--font-main); font-weight: 600; font-size: 30px;
    color: var(--brand-blue); line-height: 1.1; text-align: center;
  }
  .legal-name { font-family: var(--font-serif); font-size: 21px; fill: #ffffff; letter-spacing: 0.5px; }

  /* Front side */
  .card-front { left: 100px; top: 520px; background: var(--card-white); }
  .card-front .brand {
    position: absolute; left: 36px; top: 40px;
    display: flex; align-items: center; gap: 12px;
  }
  .card-front .brand-name { font-size: 26px; text-align: left; }
  .person { position: absolute; left: 40px; top: 140px; }
  .person-name {
    font-size: 22px; color: var(--brand-blue); font-variant: small-caps; letter-spacing: 1px;
  }
  .person-role {
    font-size: 13px; color: var(--ink); font-variant: small-caps; letter-spacing: 1px; margin-top: 6px;
  }
  .contact { position: absolute; left: 330px; top: 120px; font-size: 15px; color: var(--ink); }
  .address { font-variant: small-caps; letter-spacing: 1px; line-height: 1.3; font-size: 17px; margin-bottom: 10px; }
  .contact-line { font-variant: small-caps; letter-spacing: 1px; line-height: 1.35; }
  .contact-label { color: var(--brand-red); }
  .email { font-family: var(--font-serif); color: var(--brand-blue); font-size: 16px; margin-top: 2px; }
</style>
</head>
<body>

<section class="card card-back" aria-label="Card back">
  <svg class="card-waves" viewBox="0 0 620 378" aria-hidden="true">
    <path d="M0,240 C170,250 380,345 620,250 L620,378 L0,378 Z" fill="var(--brand-red)"/>
    <path d="M240,290 C380,340 500,320 620,244 L620,262 C490,338 380,350 240,290 Z" fill="var(--brand-sky)"/>
  </svg>
  <div class="brand">
    <span class="brand-dot"></span>
    <span class="brand-name">Bramblecourt Holdings<br>Australia</span>
  </div>
  <svg class="card-waves" viewBox="0 0 620 378">
    <path id="legal-curve" d="M40,285 C170,292 300,330 460,350" fill="none"/>
    <text class="legal-name"><textPath href="#legal-curve">Bramblecourt Holdings Australia Pty Ltd</textPath></text>
  </svg>
</section>

<section class="card card-front" aria-label="Card front">
  <svg class="card-waves" viewBox="0 0 620 378" aria-hidden="true">
    <path d="M0,255 C180,258 380,345 620,300 L620,378 L0,378 Z" fill="var(--brand-red)"/>
    <path d="M0,245 C180,248 380,332 620,284 L620,300 C380,345 180,258 0,255 Z" fill="var(--brand-blue)"/>
  </svg>
  <div class="brand">
    <span class="brand-dot"></span>
    <span class="brand-name">Bramblecourt Holdings<br>Australia</span>
  </div>
  <div class="person">
    <div class="person-name">Dana Whitfield</div>
    <div class="person-role">Managing Director</div>
  </div>
  <div class="contact">
    <div class="address">14 Larkspur Lane<br>Tarneit VIC 3030</div>
    <div class="contact-line"><span class="contact-label">Telephone :</span> +61 3 9555 0182</div>
    <div class="contact-line"><span class="contact-label">Mobile :</span> 0400 555 218</div>
    <div class="email">dana.whitfield@bramblecourt.com.au</div>
  </div>
</section>

</body>
</html>
```